Maple Beacon Website

We are starting a marketing company and to do that we need a website! We want a website that will inspire and persuade to bring out the awesomeness in our clients.
What we want to see:
- Inspirational and persuasive imagery that relate to Branding.
- No cliche images eg. business man, suits and hand shakes
- We want to transform and educate our clients.
- We want to show them the path and would like our website to really act as a guide that guides them step by step through our process.
- We want the portray that we are an investment but not have a pretentious way to it. We put our heart into every project and that is how we treat our clients.
-When you submit your design please include what platform you have created for. Preference would be Wordpress or Joobla.

We have included the psd file for the wire frame, logo files, font files, site map and a link to a video we create to give you more information on what we would like to see. http://clipvault.example/t/qk82LmZpr

Feel free to make small modification to the logos if you think it will improve it. Your creativity and advice is most welcome.
Updates

One thing we forgot. We would like to have our contact information near the top of the website as well as at the bottom.  Here is out contact info:

Email: info@maplebeacon.example
Phone: 587-555-0142

Project Deadline Extended
Reason: As we are new with the platform and that we want to optimize our results, we decided to extend the deadline by 15 days. Thanks!

Target Market(s)

28-60, Male and Female, Oil field, Local Businesses, Dentists, Chiropractors, Hair salon, Construction/Renovation, Events etc

Industry/Entity Type

Investment

Requirements
Must have
• - 4 Inspirational and persuasive Imagery for the top portion of the website
- Must have a feel as if your not on a website an example of this is linked below.
http://www.artbidhub.example/design/402957/web-design-by-lena-torvik
Nice to have
• - Creative advice from you.
- Creative buttons for Get Free Quote and Subscribe buttons. Something out of the box that draws peoples attention. eg. a 'B' button. Just and example but still something related to branding.
Should not have
• No Cliches

```html
<!DOCTYPE html>
<html lang="en">
<head>
<meta charset="utf-8">
<title>Maple Beacon</title>
<link href="https://fonts.googleapis.com/css2?family=Nunito:wght@800;900&family=PT+Sans+Narrow:wght@700&family=Source+Sans+3:wght@400;600&display=swap" rel="stylesheet">
<style>
:root{
  --ink:#3d4148;
  --body:#4a4e55;
  --navy:#1f2a3a;
  --green:#8ab92a;
  --green-dark:#5f9a0c;
  --slate:#525b69;
  --band:#f1f2f3;
  --sky-top:#4aa6e6;
  --sky-mid:#8cc8f0;
  --rule:#c9ccd1;
}
*{box-sizing:border-box;margin:0;padding:0}
html,body{width:1200px;height:1057px;overflow:hidden;background:#fff}
body{position:relative;font-family:"Source Sans 3",Arial,sans-serif;color:var(--body)}

.site-header{position:absolute;left:0;top:0;width:1200px;height:129px;background:#fff}
.brand{position:absolute;left:55px;top:30px;display:flex;align-items:center;gap:10px}
.brand-mark{width:34px;height:34px;background:var(--green)}
.brand-name{font-family:"Source Sans 3",Arial,sans-serif;font-weight:600;font-size:34px;color:#6b6f75;letter-spacing:-.5px}
.brand-tag{position:absolute;left:88px;top:93px;font-size:16px;font-weight:600;color:#555}
.main-nav{position:absolute;right:63px;top:66px;display:flex}
.main-nav a{font-size:21px;color:var(--ink);text-decoration:none;padding:0 20px;border-left:1px solid var(--rule);line-height:26px}
.main-nav a:first-child{border-left:0}
.main-nav a:last-child{padding-right:0}

.hero{position:absolute;left:0;top:129px;width:1200px;height:376px;background:linear-gradient(180deg,var(--sky-top),var(--sky-mid) 60%,#d9ecf8)}
.hero-art{position:absolute;left:470px;top:12px;width:530px;height:364px;border-radius:260px 260px 0 0;background:radial-gradient(ellipse at 50% 60%,#fdfdfd 0,#eef5fb 55%,rgba(238,245,251,0) 75%)}
.hero-art::after{content:"";position:absolute;left:75px;top:18px;width:381px;height:346px;background:linear-gradient(90deg,#2fb44a,#e02b9b 25%,#1ea0d8 45%,#f26a1b 60%,#f4e120 75%,#a7cc2b 88%,#1e73c8)}
.hero-arrows{position:absolute;left:1104px;top:332px;display:flex;gap:8px}

.side-menu{position:absolute;left:37px;top:129px;width:282px;height:376px;background:var(--slate)}
.side-menu ul{list-style:none;padding-top:34px}
.side-menu li{height:43.5px;display:flex;align-items:center;padding-left:44px;border-bottom:1px solid rgba(255,255,255,.07);width:250px}
.side-menu li svg{margin-right:9px}
.side-menu a{font-family:"PT Sans Narrow",Arial,sans-serif;font-weight:700;font-size:23px;color:#fff;text-decoration:none}
.connect{position:absolute;left:49px;top:281px;font-family:"PT Sans Narrow",Arial,sans-serif;font-weight:700;font-size:19px;color:#d8dbe0}
.social{position:absolute;left:47px;top:316px;display:flex;gap:7px}
.social span{width:30px;height:30px;border-radius:3px;background:#4e8fd0}

.newsletter{position:absolute;left:0;top:505px;width:1200px;height:67px;background:var(--band)}
.newsletter p{position:absolute;left:353px;top:20px;font-size:21px;color:var(--ink)}
.newsletter .email{position:absolute;left:804px;top:15px;width:225px;height:37px;border:1px solid #c8cbd0;background:#fff;font-size:13px;color:#555;padding:9px 11px}
.newsletter .subscribe{position:absolute;left:1028px;top:15px;width:101px;height:37px;background:linear-gradient(#8cc63a,var(--green-dark));color:#fff;font-family:"PT Sans Narrow",Arial,sans-serif;font-weight:700;font-size:16px;text-align:center;line-height:37px}

.welcome{position:absolute;left:39px;top:618px;width:740px}
.welcome h1{font-family:Nunito,Arial,sans-serif;font-weight:900;font-size:25px;color:var(--green);letter-spacing:-.2px;margin-bottom:6px}
.welcome h1 span{color:var(--navy)}
.welcome p{font-size:15.5px;line-height:26.4px;margin-bottom:14px}

.divider{position:absolute;left:808px;top:621px;width:14px;height:234px;background:linear-gradient(90deg,rgba(0,0,0,.06),rgba(0,0,0,0));}

.quote{position:absolute;left:852px;top:620px;width:295px}
.quote h2{font-family:Nunito,Arial,sans-serif;font-weight:900;font-size:21px;color:var(--navy);margin-bottom:8px}
.quote p{font-size:15.5px;line-height:26px}
.quote-btn{position:absolute;left:852px;top:756px;width:165px;height:42px;background:linear-gradient(#8cc63a,var(--green-dark));color:#fff;font-family:"PT Sans Narrow",Arial,sans-serif;font-weight:700;font-size:18px;display:flex;align-items:center;padding-left:12px;gap:6px}

.site-footer{position:absolute;left:0;top:926px;width:1200px;height:131px;background:linear-gradient(#f1f2f3,#fff)}
.footer-nav{position:absolute;top:46px;width:100%;text-align:center;font-size:17px;color:#333}
.footer-nav a{color:#333;text-decoration:none}
.footer-nav i{font-style:normal;margin:0 9px}
.copyright{position:absolute;top:82px;width:100%;text-align:center;font-size:14.5px;color:#555}
</style>
</head>
<body>
<header class="site-header">
  <div class="brand"><span class="brand-mark"></span><span class="brand-name">Maple Beacon</span></div>
  <div class="brand-tag">Because You´re Awesome!</div>
  <nav class="main-nav"><a>Maple Beacon</a><a>Be Found</a><a>Connect</a><a>Get Growing</a></nav>
</header>

<section class="hero">
  <div class="hero-art" role="img" aria-label="Colourful raised hands holding communication icons in front of a white cloud"></div>
  <div class="hero-arrows">
    <svg width="14" height="22" viewBox="0 0 14 22"><path d="M11 2 3 11l8 9" fill="none" stroke="#3b3f46" stroke-width="2.5"/></svg>
    <svg width="14" height="22" viewBox="0 0 14 22"><path d="M3 2l8 9-8 9" fill="none" stroke="#3b3f46" stroke-width="2.5"/></svg>
  </div>
</section>

<aside class="side-menu">
  <ul>
    <li><svg width="8" height="12" viewBox="0 0 8 12"><path d="M1 1l5 5-5 5" fill="none" stroke="#cfd3d9" stroke-width="1.5"/></svg><a>STRATEGY</a></li>
    <li><svg width="8" height="12" viewBox="0 0 8 12"><path d="M1 1l5 5-5 5" fill="none" stroke="#cfd3d9" stroke-width="1.5"/></svg><a>PORTFOLIO</a></li>
    <li><svg width="8" height="12" viewBox="0 0 8 12"><path d="M1 1l5 5-5 5" fill="none" stroke="#cfd3d9" stroke-width="1.5"/></svg><a>ABOUT US</a></li>
    <li><svg width="8" height="12" viewBox="0 0 8 12"><path d="M1 1l5 5-5 5" fill="none" stroke="#cfd3d9" stroke-width="1.5"/></svg><a>CONTACT US</a></li>
    <li><svg width="8" height="12" viewBox="0 0 8 12"><path d="M1 1l5 5-5 5" fill="none" stroke="#cfd3d9" stroke-width="1.5"/></svg><a>BLOG</a></li>
  </ul>
  <div class="connect">CONNECT WITH US!</div>
  <div class="social"><span></span><span></span><span></span><span></span></div>
</aside>

<section class="newsletter">
  <p>Get Tips and Tricks! Subscribe to Our Newsletter.</p>
  <div class="email">email address</div>
  <div class="subscribe">SUBSCRIBE</div>
</section>

<main class="welcome">
  <h1>WELCOME TO <span>MAPLE BEACON</span> MAINPAGE</h1>
  <p>Nunc tempus felis vitae urna. Vivamus porttitor, g, purus nisi eleifend libero, a tempus libero lectus feugiat felis. Morbi diam mauris, viverra in, gravida eu, mattis in, ante. Morbi eget arcu. Morbi porta, libero id ullamcor-per nonummy, nibh ligula pulvinar metus, eget consectetuer augue nisi quis lacus. Ut ac mi quis lacus mollis aliquam. Curabitur iaculis tempus eros. Curabitur vel mi sit amet magna malesuada ultrices.</p>
  <p>Maecenas aliquet velit vel turpis. Mauris neque metus, malesuada nec, ultricies sit amet, porttitor mattis, enim. In massa libero, interdum nec, interdum vel, blandit sed, nulla. In ullamcorper, est eget tempor cursus, neque mi consectetuer mi, a ultricies massa est sed nisl.</p>
</main>

<div class="divider"></div>

<section class="quote">
  <h2>GET A QUOTE NOW</h2>
  <p>Lamcorper nonummy, nibh ligula pulvinar metus, eget consectetuer augue nisi quis lacus. Ut ac mi quis lacus mo</p>
</section>
<div class="quote-btn"><svg width="7" height="12" viewBox="0 0 7 12"><path d="M1 1l5 5-5 5" fill="none" stroke="#3f6e08" stroke-width="2"/></svg>GET A FREE QUOTE</div>

<footer class="site-footer">
  <div class="footer-nav"><a>Sitemap</a><i>|</i><a>Strategy</a><i>|</i><a>Portfolio</a><i>|</i><a>About Us</a><i>|</i><a>Contact Us</a><i>|</i><a>Blog</a></div>
  <div class="copyright">© Maple Beacon Inc. 2013 &nbsp;|&nbsp; Term of Use</div>
</footer>
</body>
</html>
```